Web Design job - NetKestrel Company including Desktop & Mobile version

Create a Web Design (Uncoded - PSD layout only)

1. About our company

NetKestrel is an Australian-based company which sells used networking devices to coporates and other brokers in USA, Europe and other countries. We are the market leader in this space and currently have warehouses in Sydney and California. Most of our products are from VORLAN.

Our competitive advantages come from lowest price in the market, flexible product configuration for different demands of customers, long time experience in the business and huge stock of inventory.

We are in need of a new website to enhance customer and partner engagement which are measured by sales metrics and website performance metrics such as number of request for a quote, number of new orders, return visits, views, conversion rate, etc.

2. Website structure:

We need different looks for different devices: Desktop, iPad and Mobile with popular screen resolutions for each of following page.

Try to make one as good as possible, then we can move further. Below are the main pages of the web:

+ Home Page: Where customers learn about the company and its business. Should have: Beautiful company profile, highlighted company contact and strengths; A comprehensive overview about selling products.

+ Category Page: Where customers learn about products in a category and do the search action. Should focus on filter and sort functions for easily finding a product.

+ Product Page: Where customers learn about the details of a specific products such as price, image, description, related products.
- Also need features for cross-sell or up-sell.
- An item may have both new and refurbished prices, or either or none of them. Should have options to choose between new or refurbished price to add to cart.

+ Information Page: About the company, Company Announcement.

+ Cart management and Check-out

+ Search results

REFERENCES
Current website: http://netkestrel.com.au/

Prefered Layout:
- https://www.gearbazaar-example.com/en/vorlan-systems/vorlan-router-series/vorlan-series-1900/vorlan-systems-vorlan1941-k9
- https://www.wiresandboxes-example.com/vorlan-2port-rj48-multiflex-t1-trunk-card-vwic2mftt1-p-1374.html
- The attached files play as wireframes, only for the purpose of guiding. You are free to make your choices of colors and layouts.

Target Market(s)

- Corporate clients
- Main market: Australia

Industry/Entity Type

It Company

Number of Pages Required

3 page

Font styles to use
Sans Serif

Requirements
Must have
• - The new design should have a clear look to easily find information while should look professional to aim at corporate clients.
• - Require least time or effort to finish a task
• - Optimize for SEO and loading time
• - Mobile version is optimized for touching, swiping and loading time.
• - Bear in mind that the new website need minimum effort of manual tasks such as updating content. We don’t have human resources for these yet.
Nice to have
• - Should have design for each scenario such as click, popup, dropdown, deactive, have/not have an object

```html
<!DOCTYPE html>
<html lang="en">
<head>
<meta charset="utf-8">
<title>NetKestrel – Networking Equipment</title>
<link rel="stylesheet" href="https://fonts.googleapis.com/css2?family=Open+Sans:wght@400;600;700;800&display=swap">
<style>
:root{
  --blue:#0f3d8c;
  --blue-dark:#0a2c68;
  --blue-deep:#071f4d;
  --blue-light:#1b58b8;
  --orange:#f26a10;
  --orange-light:#ff8a2a;
  --yellow:#f6c21b;
  --red:#e02424;
  --ink:#2b2b2b;
  --line:#e3e3e3;
  --white:#fff;
}
*{box-sizing:border-box;margin:0;padding:0}
html,body{width:1200px;height:2708px;overflow:hidden}
body{font-family:"Open Sans",Arial,sans-serif;color:var(--ink);background:var(--white);position:relative}
.container{width:1000px;margin:0 auto;position:relative}

/* header */
.topbar{height:88px;display:flex;align-items:center;justify-content:space-between;width:1100px;margin:0 auto}
.brand{display:flex;align-items:center;gap:12px;font-weight:800;font-size:34px;color:var(--blue)}
.brand .dot{width:38px;height:38px;border-radius:50%;background:var(--orange)}
.search{display:flex;align-items:center;width:360px;height:32px;border:1px solid #cfd4dc;border-radius:16px;padding-left:14px;font-size:12px;color:#999}
.search .placeholder{flex:1}
.search .btn{width:30px;height:30px;flex:none;border-radius:50%;background:var(--blue);display:flex;align-items:center;justify-content:center;margin-right:-1px}
.contacts{display:flex;gap:22px;font-size:12px;color:#444;align-items:center}
.contacts div{display:flex;align-items:center;gap:6px}

/* nav */
.nav{height:52px;background:linear-gradient(#1b58b8,#0f3d8c);display:flex;align-items:center;justify-content:space-between;width:1000px;margin:0 auto}
.nav ul{list-style:none;display:flex;height:100%}
.nav li{color:#fff;font-size:14px;font-weight:600;padding:0 20px;display:flex;align-items:center}
.nav li.active{background:var(--yellow);color:var(--blue-deep)}
.nav .quote{color:#fff;font-size:14px;font-weight:600;padding-right:18px;display:flex;align-items:center;gap:14px}

/* hero */
.hero{height:460px;background:linear-gradient(#f6f7f9,#e4e7ec);position:relative}
.hero-visual{position:absolute;left:370px;top:30px;width:470px;height:360px;border-radius:8px;background:linear-gradient(135deg,#4a4f58,#1f2227)}
.sale{position:absolute;left:770px;top:200px;width:150px;height:150px;border-radius:50%;background:radial-gradient(circle at 40% 35%,var(--orange-light),var(--orange));color:#fff;text-align:center;padding-top:32px;box-shadow:0 6px 16px rgba(0,0,0,.25)}
.sale .s1{font-size:16px;font-weight:600}
.sale .s2{font-size:46px;font-weight:800;line-height:1}
.sale .s3{font-size:11px;margin-top:6px;display:inline-block;background:rgba(0,0,0,.2);padding:2px 10px;border-radius:10px}
.dots{position:absolute;bottom:22px;left:0;right:0;display:flex;justify-content:center;gap:10px}
.dots i{width:10px;height:10px;border-radius:50%;background:#bbb}
.dots i.on{background:var(--red)}

/* categories */
.section-title{text-align:center;font-size:22px;font-weight:600;color:#333;padding-top:74px}
.categories{display:flex;justify-content:space-between;margin-top:30px}
.cat{width:186px;height:186px;border-radius:50%;border:2px solid var(--line);display:flex;align-items:center;justify-content:center;position:relative;background:#fff}
.cat.active{border:4px solid var(--blue-light)}
.cat .thumb{width:110px;height:70px;border-radius:6px;background:linear-gradient(#9aa3ad,#4d545c)}
.cat .label{position:absolute;top:58px;left:8px;background:#fff;border-radius:12px;padding:3px 10px;font-size:12px;font-weight:700;color:var(--blue);box-shadow:0 2px 6px rgba(0,0,0,.2)}

/* products */
.products-bar{margin-top:52px;height:62px;background:linear-gradient(90deg,var(--orange),var(--orange-light));display:flex;align-items:center;justify-content:space-between;padding:0 24px}
.products-bar h2{color:#fff;font-size:20px;font-weight:600}
.tabs{display:flex;gap:8px;background:#fff;padding:6px 8px;border-radius:18px}
.tabs span{font-size:12px;padding:4px 16px;border-radius:14px;color:#555}
.tabs span.on{background:var(--blue-deep);color:#fff}
.cards{display:flex;justify-content:space-between;margin-top:32px}
.card{width:220px;height:336px;border:1px solid var(--line);position:relative;text-align:center}
.card .img{height:200px;margin:10px;border-radius:3px;background:linear-gradient(135deg,#7c858f,#2f353c)}
.card .name{font-size:13px;color:#444;line-height:1.45;margin-top:8px}
.card .price{font-size:16px;font-weight:700;margin-top:8px;color:#222}
.card.hover .info{position:absolute;left:0;right:0;bottom:0;height:116px;background:#1c1c1c;color:#fff;padding-top:10px}
.card.hover .info .name,.card.hover .info .price{color:#fff}
.tag{position:absolute;left:12px;top:12px;width:48px;height:48px;border-radius:50%;background:var(--red);color:#fff;font-size:11px;font-weight:700;display:flex;align-items:center;justify-content:center;line-height:1.1;text-align:center}

/* stats */
.about{margin-top:48px;height:412px;background:linear-gradient(var(--blue),var(--blue-dark));color:#fff;text-align:center}
.stats{display:flex;justify-content:space-around;padding:34px 60px 0}
.stat b{display:block;font-size:44px;font-weight:400;line-height:1.1}
.stat span{display:block;font-size:12px;line-height:1.4;margin-top:8px}
.about hr{border:0;border-top:1px solid rgba(255,255,255,.25);margin:32px 0 0}
.about h3{font-size:17px;font-weight:600;margin-top:22px}
.about p{font-size:11.5px;line-height:1.7;width:860px;margin:14px auto 0;opacity:.9}
.btn-yellow{display:inline-block;margin-top:20px;background:var(--yellow);color:var(--blue-deep);font-size:12px;font-weight:600;padding:6px 22px;border-radius:14px}

/* request quote */
.quote-sec{height:440px;margin-top:20px;position:relative}
.agent{position:absolute;left:60px;top:0;width:380px;height:440px;border-radius:190px 190px 0 0;background:linear-gradient(#f2d6c4,#8fb3e0)}
.quote-text{position:absolute;left:560px;top:138px;width:440px}
.quote-text h4{font-size:20px;font-weight:400;color:#333}
.quote-text .phone{font-size:30px;font-weight:600;color:var(--blue);margin-top:6px}
.quote-text p{font-size:12px;color:#666;line-height:1.5;margin-top:8px}
.quote-text .email{font-size:28px;font-weight:600;color:var(--blue);margin-top:4px;white-space:nowrap}

/* policy strip */
.strip{height:110px;background:var(--blue);margin-top:40px}
.strip .container{display:flex;height:100%}
.strip .item{flex:1;display:flex;align-items:center;justify-content:center;gap:14px;color:#fff;font-size:18px;font-weight:600;letter-spacing:.5px}
.strip .item:nth-child(1),.strip .item:nth-child(3){background:var(--orange)}
.strip .item:nth-child(2){background:var(--orange-light)}

/* footer */
.footer{height:202px;background:var(--blue-dark);color:#fff}
.footer .container{display:flex;justify-content:space-between;padding-top:22px}
.col{width:290px}
.col h5{font-size:15px;font-weight:700;margin-bottom:12px}
.col p,.col li{font-size:10.5px;line-height:1.6;opacity:.85;list-style:none}
.badges{display:flex;gap:10px;margin-top:12px}
.badges i{width:44px;height:22px;border-radius:3px;background:#fff;opacity:.85}
.col li{display:flex;align-items:center;gap:10px;margin-bottom:7px}
.col li i{width:22px;height:22px;border-radius:3px;background:rgba(255,255,255,.2);flex:none}
.bottom{height:48px;background:var(--blue-deep);color:#9fb1d6;font-size:11px;text-align:center;line-height:48px}
</style>
</head>
<body>

<header class="topbar">
  <div class="brand"><span class="dot"></span>NetKestrel</div>
  <div class="search"><span class="placeholder">Search entire store here...</span>
    <span class="btn"><svg width="14" height="14" viewBox="0 0 14 14"><circle cx="6" cy="6" r="4.2" fill="none" stroke="#fff" stroke-width="1.8"/><line x1="9" y1="9" x2="13" y2="13" stroke="#fff" stroke-width="1.8"/></svg></span>
  </div>
  <div class="contacts">
    <div><svg width="14" height="14" viewBox="0 0 14 14"><path d="M3 1l3 3-1.5 1.5a8 8 0 004 4L10 8l3 3-2 2C6 13 1 8 1 3z" fill="#0f3d8c"/></svg>Call Us: (061) 02 5550 1420</div>
    <div><svg width="14" height="12" viewBox="0 0 14 12"><rect x="1" y="1" width="12" height="10" fill="none" stroke="#0f3d8c" stroke-width="1.4"/><path d="M1 1l6 5 6-5" fill="none" stroke="#0f3d8c" stroke-width="1.4"/></svg>sales@netkestrel.example</div>
    <div><svg width="16" height="14" viewBox="0 0 16 14"><path d="M1 1h3l2 8h8l1-6H5" fill="none" stroke="#0f3d8c" stroke-width="1.5"/><circle cx="7" cy="12" r="1.3" fill="#0f3d8c"/><circle cx="13" cy="12" r="1.3" fill="#0f3d8c"/></svg>Cart (0)</div>
  </div>
</header>

<nav class="nav">
  <ul>
    <li class="active">Home</li><li>Products</li><li>Switches</li><li>Wireless</li><li>IP Phones</li><li>Accessories</li>
  </ul>
  <div class="quote">Request a Quote
    <svg width="18" height="16" viewBox="0 0 16 14"><path d="M1 1h3l2 8h8l1-6H5" fill="none" stroke="#fff" stroke-width="1.5"/><circle cx="7" cy="12" r="1.3" fill="#fff"/><circle cx="13" cy="12" r="1.3" fill="#fff"/></svg>
  </div>
</nav>

<section class="hero">
  <div class="hero-visual" role="img" aria-label="Router and rack-mounted network equipment product shot"></div>
  <div class="sale"><div class="s1">Save Upto</div><div class="s2">40%</div><span class="s3">Shop Now</span></div>
  <div class="dots"><i></i><i class="on"></i><i></i></div>
</section>

<main class="container">
  <h2 class="section-title">Product Categories</h2>
  <div class="categories">
    <div class="cat active"><div class="thumb" role="img" aria-label="Wireless access point"></div><span class="label">Wireless Securities</span></div>
    <div class="cat"><div class="thumb" role="img" aria-label="Network switch"></div></div>
    <div class="cat"><div class="thumb" role="img" aria-label="IP phones"></div></div>
    <div class="cat"><div class="thumb" role="img" aria-label="Cables"></div></div>
    <div class="cat"><div class="thumb" role="img" aria-label="Transceiver modules"></div></div>
  </div>

  <div class="products-bar">
    <h2>Our Products</h2>
    <div class="tabs"><span class="on">Best Price</span><span>Best Sale</span><span>New Products</span><span>Promotion</span></div>
  </div>

  <div class="cards">
    <div class="card"><div class="img" role="img" aria-label="Router module board"></div><div class="name">NKR-MOD-2044<br>Refurbished</div><div class="price">$500.00</div></div>
    <div class="card"><div class="img" role="img" aria-label="Network interface card"></div><div class="name">NKC-LINK-88E<br>Brand New</div><div class="price">$1,200.00</div></div>
    <div class="card hover"><div class="img" role="img" aria-label="Wireless router"></div><span class="tag">40%<br>OFF</span>
      <div class="info"><div class="name">VORLAN 4120-R<br>Refurbished</div><div class="price">$245.00</div></div></div>
    <div class="card"><div class="img" role="img" aria-label="Rack-mount router"></div><div class="name">VORLAN 860-S<br>Refurbished</div><div class="price">$285.00</div></div>
  </div>

  <section class="about">
    <div class="stats">
      <div class="stat"><b>7</b><span>Years Of Experience</span></div>
      <div class="stat"><b>99.5%</b><span>Positive Feedback<br>On TradeHub</span></div>
      <div class="stat"><b>300</b><span>Clients &amp; Partners<br>Around the World</span></div>
      <div class="stat"><b>1,250</b><span>SKUs In Inventory</span></div>
    </div>
    <hr>
    <h3>Welcome To NetKestrel</h3>
    <p>We are an Australian supplier of quality used and new networking equipment for corporate clients and brokers worldwide. With warehouses in Sydney and California, we keep a large stock of routers, switches, wireless gear and IP phones ready to ship. Every unit is tested by our technicians and backed by our warranty. Our team offers flexible configurations to match your exact needs, fast quotes, and the lowest prices in the market, so you can build and grow your network with confidence and without delay.</p>
    <span class="btn-yellow">Read more</span>
  </section>
</main>

<section class="container quote-sec">
  <div class="agent" role="img" aria-label="Customer support agent with headset"></div>
  <div class="quote-text">
    <h4>Request a Quote</h4>
    <div class="phone">(061) 02 5550 1420</div>
    <p>Call today for a great price on new and used<br>networking equipment</p>
    <p>Or Email to:</p>
    <div class="email">sales@netkestrel.example</div>
  </div>
</section>

<section class="strip">
  <div class="container">
    <div class="item"><svg width="26" height="26" viewBox="0 0 26 26"><path d="M13 2l9 4v7c0 6-4 9-9 11-5-2-9-5-9-11V6z" fill="none" stroke="#fff" stroke-width="2"/></svg>WARRANTY</div>
    <div class="item"><svg width="26" height="26" viewBox="0 0 26 26"><rect x="5" y="11" width="16" height="12" rx="2" fill="none" stroke="#fff" stroke-width="2"/><path d="M9 11V7a4 4 0 018 0v4" fill="none" stroke="#fff" stroke-width="2"/></svg>PRIVACY STATEMENT</div>
    <div class="item"><svg width="26" height="26" viewBox="0 0 26 26"><rect x="5" y="3" width="16" height="20" fill="none" stroke="#fff" stroke-width="2"/><path d="M9 9h8M9 13h8M9 17h5" stroke="#fff" stroke-width="2"/></svg>TERMS OF TRADE</div>
  </div>
</section>

<footer class="footer">
  <div class="container">
    <div class="col">
      <h5>About Us</h5>
      <p>NetKestrel supplies tested networking gear to businesses across Australia and abroad. We focus on fair prices, fast shipping and honest advice from people who know the products well.</p>
      <div class="badges"><i></i><i></i><i></i><i></i></div>
    </div>
    <div class="col">
      <h5>Contact Us</h5>
      <ul>
        <li><i></i>1-800-555-0198 (Phone)</li>
        <li><i></i>02 5550 1421 (Fax)</li>
        <li><i></i>support@netkestrel.example</li>
        <li><i></i>12 Harbour Lane, Sydney NSW 2000</li>
      </ul>
    </div>
    <div class="col">
      <h5>Why Us</h5>
      <ul>
        <li><i></i>100% Wholesale Price</li>
        <li><i></i>100% Quality Assurance</li>
        <li><i></i>Free Support</li>
        <li><i></i>100% Moneyback Guarantee</li>
        <li><i></i>Flexible Options</li>
      </ul>
    </div>
  </div>
</footer>
<div class="bottom">© 2017 NetKestrel. All rights reserved. Terms of Use</div>

</body>
</html>
```